Car rental website design for a UAE car rental company

This project is about creating a new website design for a car rental company located in Dubai (United Arab Emirates), I opened the same project a few months ago but I didn't receive a lot of appealing entries so I closed it but this time I am marking the project as guaranteed to avoid such situation again, if you have already provided a design before then please re-submit again on this project so that it is considered while reviewing all the designs

A few important things:

1- We need a simple non-complex design
2- The final deliverable would be 2 screens (PSD, JPEG ... etc), the first screen is for the home page and the second screen is for an internal page
3- The home page must have a section that end users can use to rent a car online directly from the home page instead of going into some inner pages
4- The current website is very old and not very appealing so avoid creating a similar design (www.crestvane-autos.example)
5- The name is Crestvane but the company rents normal cars (no Limousin cars will be rented) so avoid adding any fancy cars in the images/graphics used in the design, just normal end users cars
6- The expected pages would be: home, About us, Our team, Strategy, Contact us and links to social media pages
7- The attachments include the company's logo and some screens from other car rental companies that provide online rentals/payments

If you have any questions please feel free to ask and please note that we will need the designs urgently

Thanks

Target Market(s)

Dubai - United Arab Emirates

Industry/Entity Type

It Company

Number of Pages Required

2 page

Font styles to use
Sans Serif

Requirements
Must have
• Check the project details
Nice to have
Should not have

```html
<!DOCTYPE html>
<html lang="en">
<head>
<meta charset="utf-8">
<title>Crestvane Rent A Car</title>
<link href="https://fonts.googleapis.com/css2?family=Roboto+Slab:wght@300;400;700&family=Open+Sans:wght@400;600&display=swap" rel="stylesheet">
<style>
:root{
  --crimson:#a4003b;
  --crimson-dark:#8c0032;
  --ink:#333;
  --grey:#7b7b7b;
  --soft:#f4f4f4;
  --line:#cfcfcf;
  --slab:'Roboto Slab', Georgia, serif;
  --sans:'Open Sans', Arial, sans-serif;
}
*{box-sizing:border-box;margin:0;padding:0}
html,body{width:1121px;height:1200px;overflow:hidden;background:#fff}
body{position:relative;font-family:var(--slab);color:var(--ink)}
.abs{position:absolute}

/* header */
.site-header{left:0;top:0;width:1121px;height:98px;background:linear-gradient(#fafafa,#e9eaea);border-bottom:2px solid var(--crimson)}
.brand{left:75px;top:14px;display:flex;align-items:center;gap:12px}
.brand-square{width:66px;height:66px;border:3px solid var(--crimson);background:#fff}
.brand-name{font:400 34px/1 var(--slab);color:var(--crimson)}
.social{display:flex;gap:9px}
.social span{width:22px;height:22px;border-radius:50%;background:#2f6fb7;border:2px solid #fff;box-shadow:0 0 0 1px #c9c9c9}
.social span:last-child{background:#c9463d}
.header-social{left:565px;top:17px}
.call{left:790px;top:10px;display:flex;align-items:center;gap:8px;color:var(--crimson);font:400 18px var(--slab)}
.main-nav{right:76px;top:66px;display:flex;gap:24px;font:300 16px var(--slab);color:var(--grey)}
.main-nav .active{color:var(--crimson);font-weight:400}

/* hero */
.hero{left:0;top:98px;width:1121px;height:410px;background:linear-gradient(100deg,#d9dde0 0%,#9ca4a8 30%,#55605f 55%,#a89a72 80%,#c8c0a2 100%)}
.hero-title{left:83px;top:130px;width:560px;font:400 29px/36px var(--slab);color:#fff}
.hero-strip{left:0;top:505px;width:1121px;height:5px;background:var(--crimson)}

.booking{left:655px;top:98px;width:390px;height:410px;background:var(--crimson);padding:8px 5px 6px}
.tabs{display:flex;height:34px;font:400 15px/34px var(--slab);color:#fff}
.tab{padding:0 10px}
.tab.active{background:#8d9694}
.booking-body{background:#f7f5f4;height:362px;position:relative;font:400 13px var(--slab);color:#333}
.step{position:absolute;left:4px;width:24px;height:24px;border:1px solid var(--crimson);background:#fff;text-align:center;font:400 14px/22px var(--slab)}
.field{position:absolute;height:26px;border:1px solid #9a9a9a;background:#fff;font:400 12px/24px var(--sans);padding-left:6px;color:#333}
.spin{position:absolute;right:0;top:0;width:20px;height:24px;border-left:1px solid #bbb;font:9px/11px var(--sans);text-align:center;color:#555}
.link{color:var(--crimson);text-decoration:underline}
.check{display:inline-block;width:9px;height:9px;border:1px solid #555;margin-right:5px;vertical-align:0}
.help{display:inline-block;width:19px;height:19px;border-radius:50%;background:#9ba49f;color:#fff;font:11px/19px var(--sans);text-align:center;vertical-align:middle}
.quote-btn{position:absolute;right:5px;bottom:-6px;width:128px;height:38px;background:var(--crimson);color:#fff;font:400 15px/38px var(--slab);text-align:center}

/* features */
.features{left:0;top:510px;width:1121px;height:253px;background:var(--soft);border-bottom:1px solid #e2e2e2}
.feature{position:absolute;top:30px;width:240px;text-align:center}
.feature-icon{width:88px;height:88px;margin:0 auto 14px;border-radius:50%;border:2px solid #8a8a8a;background:#fff;display:flex;align-items:center;justify-content:center}
.feature-icon.hot{border-color:var(--crimson)}
.feature h3{font:400 15px/20px var(--slab);color:#333;margin-bottom:6px}
.feature p{font:400 14px/19px var(--sans);color:#444}

/* content */
.section-title{font:300 18px var(--slab);color:#7a8580;padding-bottom:8px;width:447px;border-bottom:1px dashed #999;margin-bottom:10px}
.section-title b{font-weight:400;color:var(--crimson)}
.copy{font:400 13.5px/21px var(--slab);color:#333}
.welcome{left:78px;top:793px;width:700px}
.read-more{display:block;margin-top:6px;font:400 14px var(--slab);color:#111}
.divider{left:78px;top:962px;width:700px;height:8px;background:radial-gradient(ellipse at center,#d6d6d6 0%,rgba(255,255,255,0) 70%)}
.mission{left:78px;top:1001px;width:700px}
.mission .copy+.copy{margin-top:4px}

.offer{position:absolute;width:205px}
.offer-photo{height:95px;border-radius:40% 40% 12px 12px}
.offer-tag{margin-top:6px;height:38px;background:var(--crimson);color:#fff;font:700 15px/38px var(--slab);text-align:center;position:relative}
.offer-tag:before{content:"";position:absolute;left:50%;top:-6px;margin-left:-6px;border:6px solid transparent;border-top:0;border-bottom-color:var(--crimson)}
.offer-a{left:834px;top:790px}
.offer-a .offer-photo{background:linear-gradient(#e4e6e8,#9aa0a5 60%,#5b6064)}
.offer-b{left:837px;top:990px}
.offer-b .offer-photo{background:linear-gradient(#f05a55,#c81818 60%,#6b0c0c)}

/* footer */
.site-footer{left:0;top:1145px;width:1121px;height:55px;background:var(--crimson);color:#fff}
.foot-nav{left:76px;top:0;display:flex;gap:18px;font:400 14px/55px var(--slab)}
.footer-social{left:622px;top:16px}
.copyright{right:45px;top:0;font:600 13px/55px var(--sans)}
</style>
</head>
<body>

<header class="site-header abs">
  <div class="brand abs"><span class="brand-square"></span><span class="brand-name">Crestvane</span></div>
  <div class="social header-social abs" aria-label="Social media links"><span></span><span></span><span></span><span></span></div>
  <div class="call abs">
    <svg width="38" height="42" viewBox="0 0 38 42" aria-hidden="true"><path d="M6 22a13 13 0 0 1 26 0" fill="none" stroke="#555" stroke-width="3"/><rect x="3" y="20" width="7" height="12" rx="3" fill="#a4003b"/><rect x="28" y="20" width="7" height="12" rx="3" fill="#a4003b"/><path d="M31 32q0 6-9 7" fill="none" stroke="#555" stroke-width="2"/></svg>
    Call us at +971 4 555 0182
  </div>
  <nav class="main-nav abs"><span class="active">HOME</span><span>ABOUT US</span><span>OUR TEAM</span><span>STRATEGY</span><span>CONTACT US</span></nav>
</header>

<section class="hero abs" role="img" aria-label="Dark saloon car driving on a road with motion-blurred sky"></section>
<h1 class="hero-title abs">Experience An Extra Mile of comfort, pleasure and leisure From the best</h1>
<div class="hero-strip abs"></div>

<form class="booking abs">
  <div class="tabs"><span class="tab active">Book A Car</span><span class="tab">View / Modify / Cancel A Reservation</span></div>
  <div class="booking-body">
    <span class="step" style="top:10px">1</span>
    <div class="abs" style="left:42px;top:12px">Pick-up Location &nbsp;(City, State or Airport Code</div>
    <div class="abs link" style="left:42px;top:34px">Previous Searches</div>
    <div class="field" style="left:42px;top:58px;width:325px">Dubai Airport - Terminal 3</div>
    <div class="abs link" style="left:42px;top:90px">Help me find a rental location</div>
    <div class="abs" style="left:42px;top:114px"><span class="check"></span>Return car to a different Northway Location &nbsp;<span class="help">?</span></div>
    <span class="step" style="top:149px">2</span>
    <div class="abs" style="left:42px;top:150px">Pick-up Date &amp; Time</div>
    <div class="field" style="left:42px;top:173px;width:160px">26/03/2015</div>
    <div class="field" style="left:207px;top:173px;width:160px">16:00<span class="spin">^<br>v</span></div>
    <div class="abs" style="left:42px;top:210px">Return Date &amp; Time</div>
    <div class="field" style="left:42px;top:233px;width:160px">26/03/2015</div>
    <div class="field" style="left:207px;top:233px;width:160px">16:00<span class="spin">^<br>v</span></div>
    <div class="abs" style="left:42px;top:270px">Hire Car Type</div>
    <div class="field" style="left:42px;top:293px;width:160px">Automatic</div>
    <div class="abs" style="left:210px;top:296px;font-size:12.5px"><span class="check"></span>Apply a discount Code<span class="help">?</span></div>
    <div class="quote-btn">Get A Quote</div>
  </div>
</form>

<section class="features abs">
  <div class="feature" style="left:68px">
    <div class="feature-icon hot"><svg width="60" height="44" viewBox="0 0 60 44" aria-hidden="true"><path d="M4 24l5-12h20l5 12v8H4z" fill="#a4003b"/><rect x="10" y="14" width="17" height="7" fill="#fff"/><circle cx="11" cy="32" r="3" fill="#fff"/><path d="M22 32l5-11h22l5 11v8H22z" fill="#a4003b" stroke="#fff" stroke-width="2"/><rect x="29" y="23" width="18" height="6" fill="#fff"/><rect x="25" y="34" width="26" height="2" fill="#fff"/></svg></div>
    <h3>Wide Range Of Vehicles For City Driving or SUV's For Trips</h3>
    <p>Lorem ipsum dolor sit aonsectetuer adipiscing elied diam nonummy</p>
  </div>
  <div class="feature" style="left:331px">
    <div class="feature-icon"><svg width="44" height="44" viewBox="0 0 44 44" aria-hidden="true"><path d="M8 22L24 6h12v12L20 34z" fill="#8a8a8a" transform="rotate(10 22 22)"/><circle cx="30" cy="13" r="3" fill="#fff"/><text x="13" y="27" fill="#fff" font-family="Arial, sans-serif" font-size="10" transform="rotate(-35 18 24)">%</text></svg></div>
    <h3>Special 10% Discount For New Customers On The First Rent</h3>
    <p>Lorem ipsum dolor sit aonsectetuer adipiscing elied diam nonummy</p>
  </div>
  <div class="feature" style="left:582px">
    <div class="feature-icon"><svg width="44" height="48" viewBox="0 0 44 48" aria-hidden="true"><circle cx="14" cy="9" r="6" fill="#8a8a8a"/><rect x="18" y="7" width="18" height="4" fill="#8a8a8a"/><path d="M6 30l5-10h22l5 10v10H6z" fill="#8a8a8a"/><rect x="12" y="22" width="20" height="6" fill="#fff"/><circle cx="12" cy="34" r="2.5" fill="#fff"/><circle cx="32" cy="34" r="2.5" fill="#fff"/></svg></div>
    <h3>Long Term Car<br>Rentals</h3>
    <p>Lorem ipsum dolor sit aonsectetuer adipiscing elied diam nonummy</p>
  </div>
  <div class="feature" style="left:831px">
    <div class="feature-icon"><svg width="40" height="40" viewBox="0 0 40 40" aria-hidden="true"><path d="M6 14l10-10v6c12 0 20 6 18 26-2-10-8-14-18-14v6z" fill="#8a8a8a"/></svg></div>
    <h3>Buyback Option After<br>Lease Term</h3>
    <p>Lorem ipsum dolor sit aonsectetuer adipiscing elied diam nonummy</p>
  </div>
</section>

<section class="welcome abs">
  <h2 class="section-title">Welcome to Crestvane <b>Rent A Car</b></h2>
  <p class="copy">As Dubai is expected to welcome millions of tourists and visitors, car rental industry is believed to escalate more rapidly in the region. Over the past five years, demands for car rentals in Dubai has been augmenting at a healthy pace and is currently registering a growth rate of 20 to 25 percent per year. The swift economic growth and the number. Crestvane was established to bring comfort and pleasure to all its clients. ...</p>
  <span class="read-more">Read More</span>
</section>
<div class="divider abs"></div>
<section class="mission abs">
  <h2 class="section-title">Our <b>Mission</b></h2>
  <p class="copy">To be one of the leading auto leasing company in the fast growing economy and tourism industry of the emirate of Dubai &amp; play alongside with the major car rental companies in the globe.</p>
  <p class="copy">Crestvane vows to deliver comfort, luxury &amp; satisfaction to all our clients by providing them professional, hassle-free and first class service.</p>
</section>

<div class="offer offer-a">
  <div class="offer-photo" role="img" aria-label="Silver saloon car"></div>
  <div class="offer-tag">From Only AED 1100 p/m</div>
</div>
<div class="offer offer-b">
  <div class="offer-photo" role="img" aria-label="Red saloon car"></div>
  <div class="offer-tag">From Only AED 1100 p/m</div>
</div>

<footer class="site-footer abs">
  <nav class="foot-nav abs"><span>HOME</span><span>ABOUT US</span><span>OUR TEAM</span><span>STRATEGY</span><span>CONTACT US</span></nav>
  <div class="social footer-social abs" aria-label="Social media links"><span></span><span></span><span></span><span></span></div>
  <div class="copyright abs">© 2015 Crestvane. All Rights Reserved</div>
</footer>

</body>
</html>
```